We are a local Communty Pharmacy wishing to promote and market a specialised Pharmaceutical Service

We would like a design that is professional and enticing ( according to the brief In attached files)
We wish to Market Compounding Pharmacy as a specialist side of our business.
We have the expertise a purpose built preparation laboratory.
The main purpose is an Internet presence that entices prospective patients to contact or visit our physical store.

Target Market(s)

Patients Medicos and Veterinary clients

Industry/Entity Type

Pharmacy

Coding

Coded - Design and coding required

Number of Pages Required

1 page

Requirements
Must have
• Clear friendly image
Nice to have
• soft enticing feel
Should not have
• No crass loud unprofessional elements

```html
<!DOCTYPE html>
<html lang="en">
<head>
<meta charset="utf-8">
<title>Kestrel Compounding Pharmacy</title>
<link rel="stylesheet" href="https://fonts.googleapis.com/css2?family=Open+Sans:wght@400;600;700;800&display=swap">
<style>
:root{
  --navy:#0d3e73;
  --blue:#1a5ca3;
  --sky:#3a8fd0;
  --gold:#f2b630;
  --ink:#444b55;
  --muted:#8a9099;
  --paper:#ffffff;
  --footer:#0f3b68;
  --footer-deep:#0a2c50;
}
*{box-sizing:border-box;margin:0;padding:0}
html,body{width:710px;height:1200px;overflow:hidden;background:var(--paper)}
body{font-family:"Open Sans",Arial,sans-serif;color:var(--ink);position:relative}

.site-header{height:62px;display:flex;align-items:center;padding:0 30px 0 58px}
.brand{display:flex;align-items:center;gap:6px;width:180px}
.brand-mark{width:14px;height:14px;background:var(--gold)}
.brand-name{font-size:11px;font-weight:700;color:var(--blue);line-height:1.15;width:120px}
.address-label{font-size:11px;font-weight:700;color:var(--blue);line-height:1.2;width:110px;margin-left:40px}
.address-text{font-size:6.5px;color:var(--muted);line-height:1.5;width:110px}
.contact-list{margin-left:12px;font-size:6.5px;color:var(--muted);line-height:1.7}
.contact-list li{list-style:none;display:flex;align-items:center;gap:5px}
.contact-list svg{width:8px;height:8px}

.main-nav{height:16px;background:var(--navy);display:flex;padding-left:62px}
.main-nav a{font-size:5.5px;font-weight:600;color:#fff;text-decoration:none;padding:0 16px;line-height:16px;letter-spacing:.3px}
.main-nav a.is-active{background:var(--gold);color:var(--navy)}

.hero{position:relative;height:222px}
.hero-photo{position:absolute;inset:0;background:linear-gradient(100deg,#8fb4d6 0%,#c9dbea 35%,#5d8bb8 70%,#2e5f91 100%)}
.hero-copy{position:absolute;top:140px;left:0;right:0;text-align:center;color:#fff}
.hero-title{font-size:28px;font-weight:700;letter-spacing:1px}
.hero-sub{font-size:13px;font-weight:600;margin-top:4px;letter-spacing:.5px}

.intro{padding:30px 60px 0}
.section-title{text-align:center;font-size:19px;font-weight:700;color:var(--blue);letter-spacing:.3px}
.section-rule{width:60px;height:2px;background:var(--gold);margin:6px auto 16px}
.intro p{font-size:6.6px;line-height:1.55;color:var(--ink);margin-bottom:6px}
.intro p.caps{text-transform:uppercase;font-weight:600}

.features{position:absolute;top:708px;left:0;right:0;padding:0 60px}
.feature-grid{display:flex;justify-content:space-between}
.feature{width:168px}
.feature-photo{height:128px}
.photo-vet{background:linear-gradient(135deg,#dfe8f0,#a9bdd0)}
.photo-scar{background:linear-gradient(135deg,#f0d9c6,#c9a086)}
.photo-thyroid{background:linear-gradient(135deg,#e8d6c8,#8fa7bd)}
.feature h3{font-size:9px;font-weight:700;color:var(--blue);margin:12px 0 5px}
.feature p{font-size:6.5px;line-height:1.6;color:var(--muted)}
.btn{display:inline-block;margin-top:10px;background:var(--gold);color:#fff;font-size:6px;font-weight:700;padding:5px 9px}

.site-footer{position:absolute;top:1006px;left:0;right:0;height:154px;background:var(--footer);color:#d8e4f0;display:flex;padding:22px 60px 0}
.footer-col h4{font-size:9px;font-weight:700;color:#fff;margin-bottom:8px}
.footer-col li{list-style:none;font-size:6.5px;line-height:1.8}
.col-welcome{width:120px}
.col-hours{width:120px}
.map{width:150px;height:104px;background:linear-gradient(135deg,#e9ebe6,#cfd6cf);margin-right:30px}
.col-contact{width:150px}
.col-contact li{display:flex;align-items:center;gap:5px}
.col-contact svg{width:8px;height:8px}
.bottom-bar{position:absolute;top:1160px;left:0;right:0;height:40px;background:var(--footer-deep);color:#a9bbd0;font-size:6.5px;text-align:center;line-height:40px}
</style>
</head>
<body>

<header class="site-header">
  <div class="brand">
    <span class="brand-mark"></span>
    <span class="brand-name">Kestrel Compounding Pharmacy</span>
  </div>
  <div class="address-label">OUR ADDRESS<br>DETAILS</div>
  <div class="address-text">Unit 4, 18 Harbour Road<br>Westvale VIC 3999<br>Monday – Saturday</div>
  <ul class="contact-list">
    <li><svg viewBox="0 0 10 10"><path d="M2 1l2 2-1 1.5a6 6 0 003 3L7.5 6l2 2-1.5 1.5C4 9 1 6 .5 1.5z" fill="#1a5ca3"/></svg>(03) 5550 1234</li>
    <li><svg viewBox="0 0 10 10"><rect x="1" y="3" width="8" height="5" fill="#1a5ca3"/><rect x="3" y="1" width="4" height="2" fill="#1a5ca3"/></svg>(03) 5550 1235</li>
    <li><svg viewBox="0 0 10 10"><rect x="1" y="2" width="8" height="6" fill="#1a5ca3"/><path d="M1 2l4 3.5L9 2" stroke="#fff" fill="none"/></svg>info@kestrelpharmacy.com.au</li>
  </ul>
</header>

<nav class="main-nav">
  <a class="is-active" href="#">HOME</a>
  <a href="#">ABOUT US</a>
  <a href="#">LOCATIONS</a>
  <a href="#">FORMULAS</a>
  <a href="#">SERVICES</a>
  <a href="#">PHARMACIES</a>
  <a href="#">CONTACT US</a>
</nav>

<section class="hero">
  <div class="hero-photo" role="img" aria-label="Pharmacist preparing medication in a laboratory"></div>
  <div class="hero-copy">
    <h1 class="hero-title">COMPOUNDING PHARMACY</h1>
    <p class="hero-sub">IS CUSTOMISED MEDICATIONS FOR PATIENTS</p>
  </div>
</section>

<section class="intro">
  <h2 class="section-title">WHAT IS COMPOUNDING PHARMACY?</h2>
  <div class="section-rule"></div>
  <p>Welcome to our compounding pharmacy, where every preparation is made to order for the individual needs of each patient.</p>
  <p>Compounding is the craft of preparing a medicine from raw ingredients when a commercial product does not suit the person who needs it.</p>
  <p>Our purpose built laboratory lets our trained pharmacists prepare creams, capsules, drops and liquids in strengths and forms that are not available off the shelf.</p>
  <p>We work closely with doctors, specialists and veterinarians to create a tailored treatment that is safe, effective and easy to take.</p>
  <p>Patients who are allergic to fillers, dyes or preservatives can receive a formula made without them.</p>
  <p>Children and pets often find flavoured liquids or soft chews far easier than tablets.</p>
  <p>Every compound is checked by a pharmacist before it leaves the laboratory, and we follow strict quality standards at every step.</p>
  <p>Please speak with your prescriber about compounding, or visit our store to talk with our team.</p>
  <p class="caps">Compounding: customised medications for every patient</p>
</section>

<section class="features">
  <h2 class="section-title">FEATURE ITEMS</h2>
  <div class="section-rule"></div>
  <div class="feature-grid">
    <article class="feature">
      <div class="feature-photo photo-vet" role="img" aria-label="Tablets and capsules spilled from a bottle"></div>
      <h3>Vet Article</h3>
      <p>Flavoured pastes and liquids that make daily dosing simple for cats, dogs and horses, prepared to the vet's exact prescription.</p>
      <span class="btn">Read More</span>
    </article>
    <article class="feature">
      <div class="feature-photo photo-scar" role="img" aria-label="Gel being applied to skin"></div>
      <h3>Scar Therapy</h3>
      <p>Silicone based gels prepared to soften and flatten scars, applied once or twice daily to help the skin heal more evenly.</p>
      <span class="btn">Read More</span>
    </article>
    <article class="feature">
      <div class="feature-photo photo-thyroid" role="img" aria-label="Patient holding the neck at the thyroid"></div>
      <h3>Thyroid Extract</h3>
      <p>Capsules made in precise strengths for patients who need a finely adjusted thyroid dose, free from common fillers and dyes.</p>
      <span class="btn">Read More</span>
    </article>
  </div>
</section>

<footer class="site-footer">
  <div class="footer-col col-welcome">
    <h4>Welcome</h4>
    <ul><li>Home</li><li>About Us</li><li>Locations</li><li>Services</li><li>Contact</li></ul>
  </div>
  <div class="footer-col col-hours">
    <h4>Hours</h4>
    <ul><li>Mon – Fri 9am – 6pm</li><li>Sat 9am – 1pm</li><li>Sun Closed</li></ul>
  </div>
  <div class="map" role="img" aria-label="Street map showing the pharmacy location"></div>
  <div class="footer-col col-contact">
    <h4>Contact Info</h4>
    <ul>
      <li><svg viewBox="0 0 10 10"><path d="M5 .5a3 3 0 00-3 3C2 6 5 9.5 5 9.5S8 6 8 3.5a3 3 0 00-3-3z" fill="#f2b630"/></svg>Unit 4, 18 Harbour Road</li>
      <li><svg viewBox="0 0 10 10"></svg>Westvale VIC 3999</li>
      <li><svg viewBox="0 0 10 10"><path d="M2 1l2 2-1 1.5a6 6 0 003 3L7.5 6l2 2-1.5 1.5C4 9 1 6 .5 1.5z" fill="#f2b630"/></svg>(03) 5550 1234</li>
      <li><svg viewBox="0 0 10 10"><rect x="1" y="3" width="8" height="5" fill="#f2b630"/><rect x="3" y="1" width="4" height="2" fill="#f2b630"/></svg>(03) 5550 1235</li>
      <li><svg viewBox="0 0 10 10"><rect x="1" y="2" width="8" height="6" fill="#f2b630"/><path d="M1 2l4 3.5L9 2" stroke="#0f3b68" fill="none"/></svg>info@kestrelpharmacy.com.au</li>
    </ul>
  </div>
</footer>
<div class="bottom-bar">© 2014 Kestrel Compounding Pharmacy. All rights reserved.</div>

</body>
</html>
```